we can communicate on this, but i want to follow the approach we took on Pellew|Marsh & Quinlan but i feel the card front needs the black background and the platinum and gold logo. The back? I am open. we can use the same info from PM&Q. Velmont Arc is an enhanced equity investment fund - basically a very exclusive boutique hedge fund that uses only stock options. very advanced things. hope you are interested

Contact Information for Business Card

Dr. Lewis T. Brennick, CFA
Scientifique de fusée financière
701.555.0143
LTBquant47@mailvantor.com

4718 Willow Creek Bend W.
West Fargo, ND 58078

No web site

Colors

Designer to choose colors to be used in the design.

Requirements
Nice to have
• I tend to prefer the most visible applications of the logo to include logo and name, the logo version with a black background and the gold and platinum components separated by the black. I see this working well for a single side (logo and name - this is card front to me).
• I am fairly open to other treatments on the reverse side with the data. To me, it makes sense to have a different color rendition of the logo on the reverse and it may be a muted black tone on tone or an oversized portion that would have spot UV. Or, the reverse may play with colors and layout
Should not have
• Other colors = no no
• Decorative font

```html
<!DOCTYPE html>
<html lang="en">
<head>
<meta charset="utf-8">
<title>Velmont Arc – Business Card</title>
<link rel="stylesheet" href="https://fonts.googleapis.com/css2?family=Montserrat:wght@800&family=Arimo:wght@400;700&display=swap">
<style>
  :root {
    --stage: #1d1d20;
    --card: #ffffff;
    --card-dark: #0d0d0e;
    --ink: #111111;
    --platinum: #dcdcdc;
    --gold: #c9a23a;
    --gold-dark: #9a7420;
    --gold-light: #f1dc8e;
    --mist: #f4f0e6;
    --mist-grey: #ececec;
  }
  * { box-sizing: border-box; margin: 0; padding: 0; }
  html, body {
    width: 1200px; height: 800px; overflow: hidden;
    background: var(--stage);
  }
  .stage {
    width: 1200px; height: 800px;
    display: flex; align-items: center; justify-content: center; gap: 30px;
  }
  .card {
    position: relative;
    width: 555px; height: 317px;
    background: var(--card);
    border-radius: 16px;
    overflow: hidden;
    box-shadow: 0 18px 40px rgba(0,0,0,.45);
  }

  /* brand lockup */
  .brand { display: flex; flex-direction: column; align-items: center; }
  .brand-dot {
    width: 86px; height: 86px; border-radius: 50%;
    background: var(--gold);
    margin-bottom: 14px;
  }
  .brand-name {
    font-family: "Montserrat", sans-serif;
    font-weight: 800;
    color: var(--ink);
    letter-spacing: 1px;
    line-height: 1;
    white-space: nowrap;
  }

  /* front */
  .card-front {
    background: var(--card-dark);
    display: flex; align-items: center; justify-content: center;
  }
  .card-front .brand-name { font-size: 44px; color: var(--platinum); }

  /* back */
  .back-mark {
    position: absolute; right: -40px; top: -70px;
    width: 330px; height: 330px; border-radius: 50%;
    background: var(--mist);
  }
  .back-mark-shade {
    position: absolute; right: 70px; top: -40px;
    width: 160px; height: 120px; border-radius: 50%;
    background: var(--mist-grey);
  }
  .card-back .brand {
    position: absolute; left: 36px; top: 40px;
    align-items: flex-start;
  }
  .card-back .brand-dot { width: 64px; height: 64px; margin-left: 8px; margin-bottom: 12px; }
  .card-back .brand-name { font-size: 26px; }

  .holder {
    position: absolute; right: 30px; top: 60px; text-align: right;
    font-family: "Arimo", sans-serif;
  }
  .holder-name { font-weight: 700; font-size: 16px; color: var(--ink); letter-spacing: .2px; white-space: nowrap; }
  .holder-role { font-size: 13px; color: var(--gold); margin-top: 4px; white-space: nowrap; }

  .divider {
    position: absolute; left: 26px; right: 26px; top: 206px;
    height: 1.5px; background: var(--ink);
  }
  .contacts {
    position: absolute; left: 30px; top: 222px;
    list-style: none;
    font-family: "Arimo", sans-serif; font-size: 14px; color: var(--ink);
  }
  .contacts li { display: flex; align-items: center; gap: 9px; height: 24px; white-space: nowrap; }
  .contact-icon {
    width: 15px; height: 15px; border-radius: 50%;
    background: var(--gold);
    display: flex; align-items: center; justify-content: center;
  }
  .address {
    position: absolute; right: 30px; top: 222px; text-align: right;
    font-family: "Arimo", sans-serif; font-size: 14px; color: var(--ink); line-height: 24px;
    white-space: nowrap;
  }
  .edge-band {
    position: absolute; left: 0; right: 0; bottom: 0; height: 9px;
    background: linear-gradient(90deg, var(--gold-dark), var(--gold-light) 45%, var(--gold) 70%, var(--gold-dark));
  }
</style>
</head>
<body>
<main class="stage">

  <section class="card card-front" aria-label="Card front">
    <div class="brand">
      <span class="brand-dot"></span>
      <span class="brand-name">VELMONT ARC</span>
    </div>
  </section>

  <section class="card card-back" aria-label="Card back">
    <span class="back-mark"></span>
    <span class="back-mark-shade"></span>

    <div class="brand">
      <span class="brand-dot"></span>
      <span class="brand-name">VELMONT ARC</span>
    </div>

    <div class="holder">
      <p class="holder-name">DR. LEWIS T. BRENNICK, CFA</p>
      <p class="holder-role">Scientifique de fusée financière</p>
    </div>

    <span class="divider"></span>

    <ul class="contacts">
      <li>
        <span class="contact-icon">
          <svg width="9" height="9" viewBox="0 0 10 10"><path d="M2 1l2 2-1 1.2c.6 1.2 1.6 2.2 2.8 2.8L7 6l2 2-1.4 1.4C4.5 9 1 5.5.6 2.4Z" fill="#fff"/></svg>
        </span>701.555.0143
      </li>
      <li>
        <span class="contact-icon">
          <svg width="9" height="9" viewBox="0 0 10 10"><rect x="1" y="2.5" width="8" height="5.5" fill="#fff"/><path d="M1 2.5l4 3 4-3" stroke="#c9a23a" stroke-width="1" fill="none"/></svg>
        </span>LTBquant47@mailvantor.com
      </li>
    </ul>

    <div class="address">
      <p>4718 Willow Creek Bend W.</p>
      <p>West Fargo, ND 58078</p>
    </div>

    <span class="edge-band"></span>
  </section>

</main>
</body>
</html>
```